Church Offering Envelope for receive weekly offerings

I need the front of an 6 3/4 envelope designed to be a church offering envelope. Our color palette is CMYK, 1a56b7, e8da7e, 19a3a3, 40c7f1, e7282d.
I need all of the text information carried forward from our old envelope (see attached) but the new style needs to be modern and flat. (Don't want another dove and clouds theme) I need a 1/4 border on all four sides as envelopes cannot be printed full bleed.
Logo is attached
Target Market(s)
Church
Industry/Entity Type
Church
Font styles to use
Sans Serif
Requirements
Must have
- must adhere to the color palette is CMYK, 1a56b7, e8da7e, 19a3a3, 40c7f1, e7282d.
- I need all of the text information carried forward from our old envelope (see attached)

```html
<!DOCTYPE html>
<html lang="en">
<head>
<meta charset="utf-8">
<title>Grace Harbor Fellowship – Offering Envelope</title>
<link rel="stylesheet" href="https://fonts.googleapis.com/css2?family=Roboto+Condensed:wght@400&family=Roboto+Slab:wght@300&display=swap">
<style>
  :root {
    --backdrop: #e9e6e2;
    --paper: #ffffff;
    --paper-shade: #f3f4f6;
    --edge: #9a9a9a;
    --red: #e7282d;
    --blue: #2b5ba8;
    --brand-blue: #1a56b7;
    --wine: #8b1a2b;
    --quote-mark: #a9cfd0;
    --rule: #c4c4c4;
  }
  * { margin: 0; padding: 0; box-sizing: border-box; }
  html, body { width: 1200px; height: 948px; overflow: hidden; }
  body {
    position: relative;
    background: var(--backdrop);
    font-family: "Roboto Condensed", "Arial Narrow", sans-serif;
  }
  .envelope-back {
    position: absolute;
    width: 973px;
    height: 460px;
    background: var(--paper);
  }
  .envelope-back--red { left: 166px; top: 30px; }
  .envelope-back--blue {
    left: 127px; top: 242px;
    background: linear-gradient(160deg, var(--paper-shade), var(--paper));
  }
  .flap { position: absolute; left: 0; top: 0; width: 973px; height: 156px; display: block; }
  .flap-name {
    position: absolute;
    left: 0; right: 0;
    top: 60px;
    text-align: center;
    color: var(--paper);
    font-size: 24px;
    letter-spacing: 0.5px;
  }
  .envelope-front {
    position: absolute;
    left: 41px; top: 427px;
    width: 975px; height: 458px;
    background: var(--paper);
    border: 1px solid var(--edge);
  }
  .front-name {
    position: absolute;
    left: 28px; top: 80px;
    color: var(--wine);
    font-size: 40px;
    letter-spacing: 0.5px;
  }
  .scripture {
    position: absolute;
    left: 530px; top: 42px;
    width: 450px;
    text-align: center;
    color: var(--blue);
    font-size: 22px;
    line-height: 31px;
    letter-spacing: 0.4px;
  }
  .scripture .mark {
    color: var(--quote-mark);
    font-size: 46px;
    line-height: 0;
    position: relative;
    top: 10px;
    letter-spacing: -4px;
  }
  .scripture .open { margin-right: 6px; }
  .scripture cite { display: block; font-style: normal; }
  .field { position: absolute; display: flex; align-items: flex-end; color: var(--red); font-size: 23px; }
  .field .line { border-bottom: 1px solid var(--rule); margin-left: auto; height: 1px; margin-bottom: 4px; }
  .field--name { left: 28px; top: 264px; width: 723px; }
  .field--name .line { width: 628px; }
  .field--tithe { left: 28px; top: 316px; width: 362px; }
  .field--tithe .line { width: 198px; }
  .field--radio { left: 420px; top: 316px; width: 336px; }
  .field--radio .line { width: 163px; }
  .notice {
    position: absolute;
    left: 28px; top: 414px;
    font-family: "Roboto Slab", Georgia, serif;
    font-weight: 300;
    font-size: 17px;
    color: var(--blue);
  }
  .notice .highlight { color: var(--red); }
</style>
</head>
<body>
  <section class="envelope-back envelope-back--red" aria-label="Envelope back, red flap">
    <svg class="flap" viewBox="0 0 973 156" aria-hidden="true">
      <path d="M0 0 H973 C964 32 958 60 898 72 L540 148 Q487 158 434 148 L76 72 C16 60 9 32 0 0Z" fill="var(--red)"/>
    </svg>
    <div class="flap-name">Grace Harbor Fellowship</div>
  </section>

  <section class="envelope-back envelope-back--blue" aria-label="Envelope back, blue flap">
    <svg class="flap" viewBox="0 0 973 156" aria-hidden="true">
      <path d="M0 0 H973 C964 32 958 60 898 72 L540 148 Q487 158 434 148 L76 72 C16 60 9 32 0 0Z" fill="var(--brand-blue)" fill-opacity="0.92"/>
    </svg>
    <div class="flap-name">Grace Harbor Fellowship</div>
  </section>

  <section class="envelope-front" aria-label="Offering envelope front">
    <div class="front-name">Grace Harbor Fellowship</div>

    <blockquote class="scripture">
      <span class="mark open">&ldquo;</span>Honour the LORD with the Substance,<br>
      and win the firt fruits of all thine<br>
      increase:<span class="mark">&rdquo;</span>
      <cite>Prov3:9</cite>
    </blockquote>

    <div class="field field--name"><span>Name</span><span class="line"></span></div>
    <div class="field field--tithe"><span>Tithe/Offering</span><span class="line"></span></div>
    <div class="field field--radio"><span>Radio/Webcast</span><span class="line"></span></div>

    <p class="notice">Grace Harbor Fellowship does not receive restricted funds in <span class="highlight">amounts less than $ 10,000</span></p>
  </section>
</body>
</html>
```